Development of the overall look and feel for the website. www.ReelPalsHub.com

This site is geared as a competitor to some of the major Fan websites. Where we want to be different is making a site geared more towards interaction with the Fans in the Social Media platform.
-Live streaming
-Instant Messaging
-Ability to request and purchase custom digital pieces
-Ability for Models/creators to sell blogs, podcasts, clips, screensavers, etc. through a dedicated online digital store.
-We will also have story like features similar to those found on Photoburst to allow interaction.
-Content Creators keep 85% of earnings

This should be sexy, seductive, bold, and geared towards all spectrums. From Swingers, Kink, Fetish, Milf, College, etc.

Overall the feeling should be Fun with a sense of excitement that is taboo and erotic while not scaring people away.

Trying to find the perfect blend between finding harmony/Norma Whitcombe/GBT/SoloPatron/Velvet Soiree and KRV. Monetization will be most similar to SoloPatron.

Target Market(s)

Target market should be 18+ / All Genders/ All sexuality. I want to be sure to target markets that were traditionally left out from some of the bigger platforms with all lifestyle and gender inclusion.

Industry/Entity Type

Adult Modeling, Adult Website, Streaming, Porn/fetish

Colors

Designer to choose colors to be used in the design.

Requirements
Must have
• Sex Appeal, Curiosity, Call to action, Storyboard to tell what we are about
Nice to have
• uploaded some designs that have overall look/feel.
Should not have
• Sexy but no nudity

```html
<!DOCTYPE html>
<html lang="en">
<head>
<meta charset="utf-8">
<title>Reel Pals Hub – Live Model</title>
<link href="https://fonts.googleapis.com/css2?family=Outfit:wght@300;400;500;600;700&display=swap" rel="stylesheet">
<style>
:root{
  --red:#c01f33;
  --purple:#7a2a70;
  --bg:#4b4b4d;
  --panel:#636365;
  --panel-light:#7a7a7c;
  --dark:#121214;
  --white:#ffffff;
  --gem:#4fd1b8;
  --gem-dark:#2a9f8c;
  --text-soft:#d8d8d8;
}
*{box-sizing:border-box;margin:0;padding:0}
html,body{width:794px;height:1200px;overflow:hidden}
body{background:var(--bg);font-family:"Outfit",sans-serif;color:var(--white);position:relative}
.abs{position:absolute}
.header{left:0;top:0;width:794px;height:53px;background:var(--red)}
.brand{left:77px;top:0;width:60px;height:53px;background:#e6e6e6;color:var(--red);font-size:8px;font-weight:600;display:flex;align-items:center;justify-content:center;text-align:center;line-height:1.1}
.nav a{position:absolute;top:17px;font-size:11px;color:var(--white);text-decoration:none}
.search{left:407px;top:14px;width:166px;height:26px;display:flex;border-radius:3px;overflow:hidden}
.search span{flex:1;background:var(--white);color:#999;font-size:9px;padding:7px 12px}
.search b{width:45px;background:var(--purple);font-weight:400;font-size:9px;padding:7px 8px}
.badge{position:absolute;top:-3px;right:-4px;width:8px;height:8px;border-radius:50%;background:var(--white);color:var(--red);font-size:6px;text-align:center;line-height:8px;font-weight:700}
.avatar-me{left:659px;top:12px;width:28px;height:28px;border-radius:50%;background:linear-gradient(135deg,#a6744f,#3b2c25);border:1px solid #d9a57a}
.toolbar{left:63px;top:89px;width:462px;height:41px;background:var(--panel);border-radius:6px}
.live-count{left:114px;top:104px;font-size:10px;font-weight:600}
.buy{left:222px;top:97px;width:124px;height:25px;background:var(--panel-light);border-radius:4px;font-size:10px;font-weight:600;padding:6px}
.next{left:434px;top:98px;width:91px;height:23px;background:var(--panel-light);border-radius:3px;font-size:9px;padding:6px 14px}
.stream{left:62px;top:143px;width:463px;height:275px;border-radius:10px;background:radial-gradient(ellipse at 60% 45%,#6c6f86 0%,#2b2d3d 40%,#0b0b12 80%)}
.play{left:266px;top:255px;width:48px;height:48px;border-radius:50%;background:rgba(150,150,150,.8)}
.pill{background:var(--purple);border-radius:12px;font-size:9px;font-weight:600;display:flex;align-items:center;justify-content:center;gap:4px}
.streamer-pic{left:76px;top:159px;width:34px;height:34px;border-radius:50%;background:linear-gradient(135deg,#777,#222);border:2px solid #f0a06c}
.live-tag{left:84px;top:187px;background:var(--red);font-size:6px;font-weight:700;padding:0 3px;border-radius:2px}
.chat{left:540px;top:68px;width:202px;height:354px;background:var(--panel);border-radius:10px;overflow:hidden}
.tabs{left:0;top:0;width:202px;height:34px;display:flex;font-size:10.5px}
.tabs div{flex:1;display:flex;align-items:center;justify-content:center}
.tab-on{background:var(--panel-light);color:#e6e6e6}
.tab-off{border-bottom:1px solid var(--panel-light)}
.bubble{position:absolute;left:40px;height:29px;background:var(--white);color:#444;font-size:6.5px;border-radius:8px 8px 8px 0;padding:10px 10px}
.chatter{position:absolute;left:13px;width:20px;height:20px;border-radius:50%;background:linear-gradient(135deg,#c89c7d,#5a3e31);border:1px solid #eee}
.typing{right:11px;top:352px;font-size:6.5px;display:flex;align-items:center;gap:4px}
.compose{left:12px;top:312px;width:179px;height:31px;background:var(--white);border-radius:6px;color:#666;font-size:8px;padding:10px 13px}
.banner{left:66px;top:449px;width:676px;height:168px;border-radius:16px;background:linear-gradient(100deg,#0d0b0c 0%,#241a17 45%,#3a2a24 70%,#140f0e 100%);z-index:2}
.banner-pic{left:34px;top:25px;width:109px;height:123px;border-radius:16px;border:1.5px solid var(--white);background:linear-gradient(135deg,#3a3d4c,#8a8d9c 60%,#1a1b22)}
.model-name{left:160px;top:27px;font-size:19px;font-weight:700}
.model-tier{left:160px;top:51px;font-size:12px;font-weight:700}
.btn{position:absolute;height:29px;border-radius:4px;font-size:11px;display:flex;align-items:center;justify-content:center;gap:6px}
.btn-purple{background:var(--purple)}
.btn-white{background:var(--white);color:var(--purple)}
.gallery{left:66px;top:603px;width:676px;height:205px;background:var(--panel);border-radius:0 0 16px 16px}
.gallery h2{position:absolute;left:31px;top:27px;font-size:15px;font-weight:400}
.photo{position:absolute;top:60px;width:118px;height:122px;border-radius:3px}
.arrow{position:absolute;top:97px;width:44px;height:44px;border-radius:50%;background:#828284;display:flex;align-items:center;justify-content:center}
.store{left:66px;top:834px;width:676px;height:61px;background:var(--red);border-radius:8px}
.cat{position:absolute;top:10px;width:70px;text-align:center;font-size:10px}
.cat svg{display:block;margin:0 auto 5px}
.gems{left:66px;top:922px;width:675px;height:172px;background:var(--panel);border-radius:8px}
.cta{left:19px;top:17px;width:117px;height:138px;background:var(--red);border-radius:8px;font-size:18px;font-weight:700;display:flex;align-items:center;justify-content:center;text-align:center;line-height:1.15}
.pack{position:absolute;top:21px;width:103px;height:135px;background:var(--dark);border:1px solid #6a3d65}
.pack h3{font-size:9.5px;font-weight:500;text-align:center;margin:8px 10px 0;padding-bottom:5px;border-bottom:1px solid #444}
.pack svg{display:block;margin:8px auto 0}
.amount{text-align:center;font-size:9.5px;font-weight:700;margin-top:4px}
.price{margin:8px auto 0;width:79px;height:20px;border:1px solid #7a3a70;font-size:9px;text-align:center;line-height:18px}
.new{position:absolute;right:6px;top:33px;width:18px;height:18px;border-radius:50%;background:var(--red);border:1px solid #fff;font-size:3.5px;font-weight:700;text-align:center;padding-top:5px;line-height:1.1}
.footer{left:0;top:1129px;width:794px;height:71px;background:var(--red);font-size:9px}
.follow{left:65px;top:28px;font-weight:600;font-size:10px;display:flex;gap:8px;align-items:center}
.follow span{font-weight:400;font-size:8px}
.copy{left:0;width:794px;top:30px;text-align:center;font-size:8px}
.code{right:20px;top:30px;font-size:8px}
</style>
</head>
<body>

<header class="abs header">
  <div class="abs brand">ReelPals<br>Hub.com</div>
  <nav class="nav">
    <a style="left:168px">Profile</a>
    <a style="left:232px">Models</a>
    <a style="left:295px">Products</a>
    <a style="left:370px">Sell</a>
  </nav>
  <div class="abs search"><span>Search Models</span><b>Search</b></div>
  <div class="abs" style="left:597px;top:19px;width:14px;height:14px">
    <svg width="14" height="14" viewBox="0 0 14 14"><path d="M7 1a4 4 0 0 0-4 4v3L1.5 10.5h11L11 8V5a4 4 0 0 0-4-4zM5.5 11.5a1.5 1.5 0 0 0 3 0z" fill="#fff"/></svg>
    <span class="badge">2</span>
  </div>
  <div class="abs" style="left:630px;top:19px;width:15px;height:14px">
    <svg width="15" height="14" viewBox="0 0 15 14"><path d="M0 1h2.5l2 7h7l2-5H4" fill="none" stroke="#fff" stroke-width="1.5"/><circle cx="5.5" cy="11.5" r="1.3" fill="#fff"/><circle cx="10.5" cy="11.5" r="1.3" fill="#fff"/></svg>
    <span class="badge">2</span>
  </div>
  <div class="abs avatar-me" role="img" aria-label="Signed-in user portrait"></div>
</header>

<section class="abs toolbar"></section>
<div class="abs" style="left:84px;top:102px">
  <svg width="20" height="14" viewBox="0 0 20 14" fill="none" stroke="#fff" stroke-width="1.3"><circle cx="10" cy="7" r="1.6" fill="#fff"/><path d="M6.5 3.5a5 5 0 0 0 0 7M13.5 3.5a5 5 0 0 1 0 7M3.5 1a9 9 0 0 0 0 12M16.5 1a9 9 0 0 1 0 12"/></svg>
</div>
<div class="abs live-count">Live 5486</div>
<div class="abs buy">Buy :
  <svg class="abs" style="left:36px;top:5px" width="16" height="15" viewBox="0 0 16 15"><rect x="0.5" y="0.5" width="15" height="14" rx="1" fill="#fff"/><rect x="0.5" y="0.5" width="15" height="3" fill="#ddd"/><text x="8" y="11" font-size="4.5" text-anchor="middle" fill="#777" font-family="Outfit,sans-serif">BLOG</text></svg>
  <svg class="abs" style="left:70px;top:4px" width="10" height="17" viewBox="0 0 10 17"><rect x="2" y="0" width="6" height="10" rx="3" fill="#fff"/><path d="M1 7a4 4 0 0 0 8 0M5 11v4M2 16h6" stroke="#fff" fill="none" stroke-width="1.2"/></svg>
  <svg class="abs" style="left:96px;top:4px" width="16" height="16" viewBox="0 0 16 16"><rect width="16" height="16" rx="1" fill="#fff"/><path d="M6 5l5 3-5 3z" fill="#777"/><rect x="1" y="1" width="2" height="2" fill="#777"/><rect x="13" y="1" width="2" height="2" fill="#777"/><rect x="1" y="13" width="2" height="2" fill="#777"/><rect x="13" y="13" width="2" height="2" fill="#777"/></svg>
</div>
<div class="abs next">Next Model <span style="margin-left:10px">›</span></div>

<section class="abs stream" role="img" aria-label="Live stream video preview of the model, blurred dark scene"></section>
<div class="abs play"><svg width="48" height="48" viewBox="0 0 48 48"><path d="M19 14l14 10-14 10z" fill="var(--purple)"/></svg></div>
<div class="abs streamer-pic" role="img" aria-label="Streamer profile photo"></div>
<div class="abs live-tag">LIVE</div>
<div class="abs" style="left:116px;top:162px;font-size:10.5px">Lousy@88 <span style="color:#f5b52e">♛</span></div>
<div class="abs" style="left:116px;top:175px;font-size:7px;font-weight:700;color:var(--red)">PRO <span style="color:var(--gem)">◆◆</span></div>
<div class="abs pill" style="left:425px;top:157px;width:86px;height:21px">Balance : 54 <span style="color:var(--gem)">◆</span></div>
<div class="abs pill" style="left:424px;top:373px;width:87px;height:26px;border-radius:5px;font-size:10px">Send Gems <span style="color:var(--gem)">◆</span></div>

<aside class="abs chat">
  <div class="abs tabs"><div class="tab-on">Group Chat</div><div class="tab-off">Private Chat</div></div>
  <div class="chatter" style="top:56px" role="img" aria-label="Chat member avatar"></div>
  <div class="bubble" style="top:51px;width:88px">Hey!.. Hi Everyone</div>
  <div class="chatter" style="top:105px" role="img" aria-label="Chat member avatar"></div>
  <div class="bubble" style="top:100px;width:72px">How are you...!!</div>
  <div class="chatter" style="top:153px" role="img" aria-label="Chat member avatar"></div>
  <div class="bubble" style="top:148px;width:61px">Im!..Fraklin!!</div>
  <div class="chatter" style="top:202px" role="img" aria-label="Chat member avatar"></div>
  <div class="bubble" style="top:197px;width:98px">Im good... How are u?</div>
  <div class="chatter" style="top:254px" role="img" aria-label="Chat member avatar"></div>
  <div class="bubble" style="top:249px;width:88px">Where are you from??</div>
  <div class="abs typing" style="top:290px">lousy@89 is typing
    <svg width="17" height="17" viewBox="0 0 17 17"><circle cx="8.5" cy="8.5" r="8.5" fill="#fff"/><circle cx="4.5" cy="9" r="1.3" fill="#333"/><circle cx="8.5" cy="6" r="1.3" fill="#333"/><circle cx="12.5" cy="9" r="1.3" fill="#333"/></svg>
  </div>
  <div class="abs compose">Write your Message
    <svg class="abs" style="right:12px;top:10px" width="13" height="11" viewBox="0 0 13 11"><path d="M0 0l13 5.5L0 11l2-5.5z" fill="var(--purple)"/></svg>
  </div>
</aside>

<section class="abs gallery">
  <h2>Model’s Photos</h2>
  <div class="arrow" style="left:28px"><svg width="10" height="16" viewBox="0 0 10 16"><path d="M8 1L2 8l6 7" stroke="#fff" stroke-width="2" fill="none"/></svg></div>
  <div class="photo" style="left:84px;background:linear-gradient(135deg,#1a1513,#3a2b24 55%,#0f0c0b)" role="img" aria-label="Model in black lace, dark studio photo"></div>
  <div class="photo" style="left:213px;background:linear-gradient(135deg,#22242e,#7d8090 55%,#15161c)" role="img" aria-label="Black and white couple portrait"></div>
  <div class="photo" style="left:342px;background:linear-gradient(135deg,#c99a7c,#2a1e1a 50%,#d2562f 75%,#1a1311)" role="img" aria-label="Lace and red rope close-up"></div>
  <div class="photo" style="left:471px;background:linear-gradient(135deg,#1a1513,#3a2b24 55%,#0f0c0b)" role="img" aria-label="Model in black lace, dark studio photo"></div>
  <div class="arrow" style="left:609px"><svg width="10" height="16" viewBox="0 0 10 16"><path d="M2 1l6 7-6 7" stroke="#fff" stroke-width="2" fill="none"/></svg></div>
</section>

<section class="abs banner" role="img" aria-label="Profile cover: lace and red rope photo">
  <div class="abs banner-pic" role="img" aria-label="Model profile photo, black and white couple"></div>
  <div class="abs model-name">Lousy@88</div>
  <div class="abs model-tier">VIP USER</div>
  <div class="btn btn-purple" style="left:564px;top:15px;width:94px;font-size:8.5px">
    <svg width="12" height="12" viewBox="0 0 12 12"><rect x="1" y="1" width="10" height="10" rx="2" fill="none" stroke="#fff" stroke-width="1.1"/></svg>View Photoburst</div>
  <div class="btn btn-purple" style="left:460px;top:119px;width:93px">View Videos</div>
  <div class="btn btn-white" style="left:564px;top:119px;width:94px">View Photos</div>
</section>

<section class="abs store">
  <div class="cat" style="left:187px">
    <svg width="20" height="20" viewBox="0 0 20 20"><rect x="0.5" y="0.5" width="19" height="19" rx="1.5" fill="#fff"/><rect x="0.5" y="0.5" width="19" height="4" fill="#eee"/><text x="10" y="14" font-size="5.5" text-anchor="middle" fill="var(--red)" font-family="Outfit,sans-serif">BLOG</text></svg>Blog</div>
  <div class="cat" style="left:253px">
    <svg width="14" height="22" viewBox="0 0 14 22"><rect x="3" y="0" width="8" height="13" rx="4" fill="#fff"/><path d="M1 9a6 6 0 0 0 12 0M7 15v5M3 21h8" stroke="#fff" fill="none" stroke-width="1.5"/></svg>Podcast</div>
  <div class="cat" style="left:319px">
    <svg width="20" height="20" viewBox="0 0 20 20"><rect width="20" height="20" rx="1" fill="#fff"/><path d="M8 6l6 4-6 4z" fill="var(--red)"/><rect x="1.5" y="1.5" width="2.5" height="2.5" fill="var(--red)"/><rect x="16" y="1.5" width="2.5" height="2.5" fill="var(--red)"/><rect x="1.5" y="16" width="2.5" height="2.5" fill="var(--red)"/><rect x="16" y="16" width="2.5" height="2.5" fill="var(--red)"/></svg>Clips</div>
  <div class="cat" style="left:389px">
    <svg width="22" height="18" viewBox="0 0 22 18"><rect x="0.5" y="0.5" width="21" height="17" fill="#fff"/><path d="M2 16l6-7 4 4 3-3 5 6z" fill="var(--red)"/><circle cx="16" cy="5" r="2" fill="var(--red)"/></svg>Screensaver</div>
</section>

<section class="abs gems">
  <div class="abs cta">Buy Now<br>or<br>Never</div>
  <div class="pack" style="left:162px"><h3>Little Gems</h3>
    <svg width="50" height="38" viewBox="0 0 50 38"><path d="M25 0l12 12-12 12-12-12z" fill="var(--gem)"/><path d="M10 17l9 9-9 9-9-9z" fill="var(--gem-dark)"/><path d="M40 17l9 9-9 9-9-9z" fill="var(--gem-dark)"/></svg>
    <div class="amount">50 GEMS</div><div class="price">$25.00</div></div>
  <div class="pack" style="left:293px"><h3>Some Gems</h3><div class="new">NEW<br>OFFER</div>
    <svg width="50" height="38" viewBox="0 0 50 38"><path d="M25 0l12 12-12 12-12-12z" fill="var(--gem)"/><path d="M10 17l9 9-9 9-9-9z" fill="var(--gem-dark)"/><path d="M40 17l9 9-9 9-9-9z" fill="var(--gem-dark)"/></svg>
    <div class="amount">150 GEMS</div><div class="price">$50.00</div></div>
  <div class="pack" style="left:423px"><h3>Bag Gems</h3><div class="new">NEW<br>OFFER</div>
    <svg width="50" height="38" viewBox="0 0 50 38"><path d="M25 0l12 12-12 12-12-12z" fill="var(--gem)"/><path d="M10 17l9 9-9 9-9-9z" fill="var(--gem-dark)"/><path d="M40 17l9 9-9 9-9-9z" fill="var(--gem-dark)"/></svg>
    <div class="amount">250 GEMS</div><div class="price">$89.00</div></div>
  <div class="pack" style="left:554px"><h3>Pack Gems</h3><div class="new">NEW<br>OFFER</div>
    <svg width="50" height="38" viewBox="0 0 50 38"><path d="M25 0l12 12-12 12-12-12z" fill="var(--gem)"/><path d="M10 17l9 9-9 9-9-9z" fill="var(--gem-dark)"/><path d="M40 17l9 9-9 9-9-9z" fill="var(--gem-dark)"/></svg>
    <div class="amount">450 GEMS</div><div class="price">$129.00</div></div>
</section>

<footer class="abs footer">
  <div class="abs follow">Follow us : <span>Facetome</span><span>Vidstream</span><span>Photoburst</span></div>
  <div class="abs copy">© copyrights 2022 Reel Pals Hub &nbsp;|&nbsp; All Rights Reserved</div>
  <div class="abs code">C54</div>
</footer>

</body>
</html>
```